The Plate Compass

Cutting Through the Noise to What Actually Works.

Nutrition book

Target Market(s)

People looking to be or get healthy and eat right.

```html
<!DOCTYPE html>
<html lang="en">
<head>
<meta charset="utf-8">
<title>The Plate Compass</title>
<link rel="stylesheet" href="https://fonts.googleapis.com/css2?family=Lexend:wght@300;400;600;700;800&display=swap">
<style>
  :root {
    --paper: #f4f1ea;
    --paper-shade: #e9e4da;
    --ink-green: #0f3a26;
    --leaf-green: #3f8a2e;
    --table-light: #c08a58;
    --table-dark: #9a6638;
    --tier-calories: #df3440;
    --tier-protein: #f07a1c;
    --tier-quality: #f1b61e;
    --tier-timing: #5aa235;
    --tier-supplements: #1d7fc4;
    --tier-noise: #6b48a6;
    --label: #ffffff;
  }
  * { margin: 0; padding: 0; box-sizing: border-box; }
  html, body { width: 800px; height: 1200px; overflow: hidden; background: var(--paper); }
  .cover {
    position: relative; width: 800px; height: 1200px; overflow: hidden;
    background: linear-gradient(180deg, #f7f5ef 0%, var(--paper) 60%, var(--paper-shade) 78%);
    font-family: 'Lexend', sans-serif;
  }
  .scene-backdrop { position: absolute; inset: 0; }
  .title-block { position: absolute; top: 22px; left: 0; width: 800px; text-align: center; }
  .title-the { font-weight: 600; font-size: 62px; line-height: 70px; color: var(--ink-green); letter-spacing: -1px; }
  .title-main { font-weight: 800; font-size: 128px; line-height: 112px; color: var(--ink-green); letter-spacing: -4px; }
  .title-accent { font-weight: 700; font-size: 128px; line-height: 124px; color: var(--leaf-green); letter-spacing: -4px; }
  .subtitle { margin-top: 22px; font-weight: 300; font-size: 31px; line-height: 42px; color: var(--ink-green); }
  .pyramid { position: absolute; inset: 0; }
  .tier-label { font-family: 'Lexend', sans-serif; font-weight: 600; font-size: 20px; fill: var(--label); letter-spacing: 0.5px; }
  .tier-icon { fill: none; stroke: var(--label); stroke-width: 2.4; stroke-linecap: round; stroke-linejoin: round; }
</style>
</head>
<body>
<main class="cover">
  <svg class="scene-backdrop" width="800" height="1200" viewBox="0 0 800 1200">
    <defs>
      <linearGradient id="tableWood" x1="0" y1="0" x2="0" y2="1">
        <stop offset="0" stop-color="var(--table-light)"/>
        <stop offset="1" stop-color="var(--table-dark)"/>
      </linearGradient>
      <radialGradient id="greenery" cx="0.5" cy="0.5" r="0.5">
        <stop offset="0" stop-color="#7fae6a" stop-opacity="0.45"/>
        <stop offset="1" stop-color="#7fae6a" stop-opacity="0"/>
      </radialGradient>
    </defs>
    <ellipse cx="40" cy="600" rx="110" ry="160" fill="url(#greenery)" role="img" aria-label="Soft-focus green houseplant"/>
    <ellipse cx="760" cy="640" rx="110" ry="150" fill="url(#greenery)" role="img" aria-label="Soft-focus green houseplant"/>
    <rect x="0" y="945" width="800" height="255" fill="url(#tableWood)" role="img" aria-label="Wooden table with tomatoes, greens and a bowl of blueberries"/>
  </svg>

  <header class="title-block">
    <div class="title-the">The</div>
    <div class="title-main">Plate</div>
    <div class="title-accent">Compass</div>
    <p class="subtitle">Cutting Through the Noise to<br>What Actually Works.</p>
  </header>

  <svg class="pyramid" width="800" height="1200" viewBox="0 0 800 1200">
    <rect x="300" y="440" width="200" height="56" rx="20" fill="#6f8f3a" opacity="0.55" role="img" aria-label="Avocado half, almonds and blueberries on top of the pyramid"/>

    <g class="tier tier-noise">
      <polygon points="118,957 682,957 695,1102 105,1102" fill="var(--tier-noise)"/>
      <path class="tier-icon" d="M382 1032 h7 l9 -8 v24 l-9 -8 h-7 z M405 1030 l12 14 M417 1030 l-12 14"/>
      <text class="tier-label" x="400" y="1085" text-anchor="middle">NOISE</text>
    </g>
    <g class="tier tier-supplements">
      <polygon points="168,875 625,875 633,980 160,980" fill="var(--tier-supplements)"/>
      <g transform="rotate(-40 400 918)"><rect class="tier-icon" x="386" y="909" width="30" height="15" rx="7.5"/><line class="tier-icon" x1="401" y1="909" x2="401" y2="924"/></g>
      <text class="tier-label" x="397" y="973" text-anchor="middle">SUPPLEMENTS</text>
    </g>
    <g class="tier tier-timing">
      <polygon points="196,781 593,781 598,879 191,879" fill="var(--tier-timing)"/>
      <circle class="tier-icon" cx="397" cy="821" r="16"/>
      <path class="tier-icon" d="M397 811 v10 l7 6"/>
      <text class="tier-label" x="397" y="869" text-anchor="middle">MEAL TIMING</text>
    </g>
    <g class="tier tier-quality">
      <polygon points="236,684 564,684 570,781 230,781" fill="var(--tier-quality)"/>
      <path class="tier-icon" d="M382 746 c0 -22 16 -36 36 -36 c0 22 -14 36 -36 36 z M382 746 l18 -18"/>
      <text class="tier-label" x="397" y="772" text-anchor="middle">FOOD QUALITY</text>
    </g>
    <g class="tier tier-protein">
      <polygon points="265,590 532,590 539,688 258,688" fill="var(--tier-protein)"/>
      <rect x="266" y="594" width="266" height="56" rx="14" fill="#d9a36a" opacity="0.7" role="img" aria-label="Grilled chicken breast, boiled egg and chickpeas"/>
      <text class="tier-label" x="397" y="675" text-anchor="middle">PROTEIN</text>
    </g>
    <g class="tier tier-calories">
      <polygon points="298,496 499,496 504,586 293,586" fill="var(--tier-calories)"/>
      <path class="tier-icon" d="M397 508 c10 10 14 18 10 26 c-2 5 -6 8 -10 8 c-6 0 -11 -5 -11 -11 c0 -6 4 -9 6 -14 c2 4 4 6 6 6 c0 -5 -2 -10 -1 -15 z"/>
      <text class="tier-label" x="397" y="575" text-anchor="middle">CALORIES</text>
    </g>
  </svg>
</main>
</body>
</html>
```